Business card design for modern PanoWalk agency

Hello,

I need a business card design for my company Kites7Market.
We mainly offer Zorvex PanoWalk Tours (360° Photography) and it should be a business card with following details:

Name: Tobias Wendler
Number: +49 176 58 20 917
Mail: tobias@kites7market.com
website: kites7market.com

Main colour that we use is the red of the logo.
It´s also important to integrate the "Zorvex Verified logo" as the person on this business card is a Zorvex verified photographer.

And if possible we would also like to integrate something like send us a sms or whatsapp and we call you back. As the number is german but we sell now in Vienna, Austria.

We offer a good price but very high photography quality, as we are mostly students - that´s our concept.

Maybe an idea is to integrate something 360° on the back-side of the card, for example the photo attached (just an idea) or some great design.
See flyer (attached) and kites7market.com for inspiration, maybe use of the photo of me (attached) in a circle or something

I´m very excited for your designs and thanks a lot in advance!! :)

Target Market(s)

Shops, hotels, shopping centers, etc. in Vienna, Austria

Industry/Entity Type

Business

Contact Information for Business Card

double-sided, use red of the logo, 360° zorvex pano walk certified photographer

Font styles to use
Serif
Sans Serif

Colors
ec1f27

Requirements
Nice to have
• maybe some 360° design on back-side
• maybe include photo of me in a circle or something or sketched in red colour

```html
<!DOCTYPE html>
<html lang="en">
<head>
<meta charset="utf-8">
<title>Tobias Wendler – Business Card</title>
<link href="https://fonts.googleapis.com/css2?family=Open+Sans:wght@400;600;700&display=swap" rel="stylesheet">
<style>
  :root {
    --page-bg: #e9eaee;
    --card-bg: #ffffff;
    --frame-line: #3a3a3a;
    --brand-red: #ec1f27;
    --deep-red: #b3121a;
    --warm-beige: #d9b98a;
    --warm-brown: #7a3f22;
    --ink: #1d1d1d;
    --muted: #6d6d6d;
    --badge-gold: #f2b632;
  }
  * { box-sizing: border-box; margin: 0; padding: 0; }
  html, body {
    width: 1200px; height: 840px; overflow: hidden;
    background: var(--page-bg);
    font-family: "Open Sans", Arial, sans-serif;
  }
  .canvas {
    width: 1200px; height: 840px;
    display: flex; align-items: center; justify-content: center;
  }
  .card {
    position: relative;
    width: 960px; height: 548px;
    background: var(--card-bg);
    box-shadow: 0 10px 30px rgba(0,0,0,0.12);
  }
  .card-frame {
    position: absolute; inset: 22px;
    border: 1.5px solid var(--frame-line);
  }
  .hero-photo {
    position: absolute; left: 23px; top: 23px; width: 914px; height: 370px;
    clip-path: polygon(0 0, 100% 0, 100% 52%, 0 100%);
    background:
      linear-gradient(200deg, rgba(236,31,39,0) 40%, rgba(236,31,39,0.85) 72%, var(--deep-red) 100%),
      linear-gradient(90deg, var(--warm-brown) 0%, #b07a4e 30%, var(--warm-beige) 60%, #e6cfa8 100%);
  }
  .person-name {
    position: absolute; left: 322px; top: 270px;
    font-size: 42px; line-height: 1; font-weight: 700; color: #fff; letter-spacing: 0.5px;
    white-space: nowrap;
    transform: rotate(-11deg); transform-origin: left bottom;
    text-shadow: 0 2px 4px rgba(0,0,0,0.25);
  }
  .portrait {
    position: absolute; left: 105px; top: 280px; width: 130px; height: 130px;
    border-radius: 50%;
    border: 4px solid #fff;
    box-shadow: 0 0 0 2px #333;
    background: radial-gradient(circle at 50% 40%, #9aa1a8 0%, #5b6168 60%, #3a3e43 100%);
  }
  .partner {
    position: absolute; left: 100px; top: 424px; width: 140px;
    display: flex; flex-direction: column; align-items: center; gap: 6px;
  }
  .partner-name { font-size: 11px; line-height: 14px; font-weight: 600; color: var(--muted); }
  .partner-badge {
    width: 56px; height: 56px; border-radius: 50%;
    background: var(--badge-gold);
  }
  .contact-list {
    position: absolute; left: 330px; top: 390px;
    list-style: none; display: flex; flex-direction: column; gap: 22px;
  }
  .contact-item {
    display: flex; align-items: center; gap: 18px;
    font-size: 24px; font-weight: 600; color: var(--ink);
  }
  .contact-icon { width: 40px; height: 40px; flex: none; }
</style>
</head>
<body>
<main class="canvas">
  <section class="card" aria-label="Business card of Tobias Wendler">
    <div class="card-frame"></div>
    <div class="hero-photo" role="img" aria-label="Panoramic interior photo of a warmly lit restaurant dining room"></div>
    <h1 class="person-name">Tobias Wendler</h1>
    <div class="portrait" role="img" aria-label="Portrait photo of Tobias Wendler"></div>
    <div class="partner">
      <span class="partner-name">Zorvex PanoWalk</span>
      <div class="partner-badge" role="img" aria-label="Zorvex Verified agency badge"></div>
    </div>
    <ul class="contact-list">
      <li class="contact-item">
        <svg class="contact-icon" viewBox="0 0 40 40" aria-hidden="true">
          <circle cx="20" cy="20" r="19" fill="var(--brand-red)"/>
          <rect x="9" y="12" width="22" height="16" rx="1.5" fill="#fff"/>
          <path d="M9.5 13 L20 21.5 L30.5 13" fill="none" stroke="var(--brand-red)" stroke-width="2"/>
        </svg>
        <span>tobias@kites7market.com</span>
      </li>
      <li class="contact-item">
        <svg class="contact-icon" viewBox="0 0 40 40" aria-hidden="true">
          <circle cx="20" cy="20" r="19" fill="var(--brand-red)"/>
          <g fill="none" stroke="#fff" stroke-width="1.8">
            <circle cx="20" cy="20" r="11"/>
            <ellipse cx="20" cy="20" rx="5" ry="11"/>
            <line x1="9" y1="20" x2="31" y2="20"/>
            <path d="M11 14.5 H29 M11 25.5 H29"/>
          </g>
        </svg>
        <span>kites7market.com</span>
      </li>
    </ul>
  </section>
</main>
</body>
</html>
```